Design a New Business Card for Our Company

We are looking for fresh, unique, and a modern business card that reflects our roots as digital marketing agency focused on SEM.

Industry/Entity Type

Marketing

Contact Information for Business Card

looking for very unique out of the box designs. clean and modern that compliments our logo

Requirements
Must have
• colors should match our logo
• Front should have name, address, email, and phone/fax of the person, phone/fax are the same number
• back should have our url

```html
<!DOCTYPE html>
<html lang="en">
<head>
<meta charset="utf-8">
<title>Clearwave Solutions – Business Card</title>
<link href="https://fonts.googleapis.com/css2?family=Roboto:wght@400;500;700&display=swap" rel="stylesheet">
<style>
  :root{
    --page:#e8e6e2;
    --paper:#f4f4f4;
    --paper-shade:#e6e6e6;
    --blue-light:#8cc3e3;
    --blue-mid:#6fa9d3;
    --blue-deep:#4a86bd;
    --rule:#b9bcc0;
    --grey-text:#9a9a9a;
    --white:#ffffff;
  }
  *{box-sizing:border-box;margin:0;padding:0}
  html,body{width:1200px;height:780px;overflow:hidden;background:var(--page);font-family:"Roboto",Arial,sans-serif}
  .canvas{position:relative;width:1200px;height:780px}

  .card{position:absolute;width:620px;height:354px;overflow:hidden;
    box-shadow:0 3px 0 #d9d9d9,0 6px 0 #cfcfcf,0 12px 24px rgba(0,0,0,.18)}

  /* Front */
  .card-front{left:60px;top:36px;background:linear-gradient(160deg,var(--white),var(--paper-shade))}
  .front-brand{position:absolute;left:0;top:0;width:100%;height:170px;display:flex;align-items:center;padding-left:70px;gap:18px}
  .brand-dot{width:46px;height:46px;border-radius:50%;background:var(--blue-mid)}
  .brand-name{font-size:46px;font-weight:700;color:var(--grey-text);letter-spacing:-1px}
  .rule{position:absolute;left:0;width:100%;height:2px;background:var(--rule)}
  .front-band{position:absolute;left:0;top:176px;width:100%;height:116px;
    background:linear-gradient(90deg,var(--blue-mid),var(--blue-light));display:flex;align-items:center;color:var(--white)}
  .contact-col{padding-left:60px;display:flex;flex-direction:column;gap:6px;font-size:17px}
  .contact-col.right{padding-left:44px}
  .person{font-weight:700;font-size:18px;letter-spacing:.3px}
  .person .role{font-weight:400;font-size:15px;border-left:1px solid var(--white);padding-left:6px;margin-left:4px}
  .line{display:flex;align-items:center;gap:8px}
  .line svg{width:18px;height:16px;flex:none}
  .divider{width:1px;height:62px;background:rgba(255,255,255,.8);margin-left:70px}
  .front-address{position:absolute;left:0;top:296px;width:100%;height:58px;display:flex;align-items:center;
    padding-left:60px;color:var(--blue-mid);font-size:17px}

  /* Back */
  .card-back{left:520px;top:396px;background:var(--paper)}
  .back-band{position:absolute;left:0;width:100%;background:linear-gradient(90deg,var(--blue-deep),var(--blue-light) 55%,var(--blue-deep))}
  .back-band.top{top:0;height:112px}
  .back-band.bottom{top:242px;height:112px}
  .back-rule{position:absolute;left:0;width:100%;height:2px;background:var(--rule)}
  .back-center{position:absolute;left:0;top:118px;width:100%;height:118px;display:flex;align-items:center;justify-content:center;
    color:var(--blue-mid);font-size:24px;letter-spacing:.5px}
</style>
</head>
<body>
<main class="canvas">

  <section class="card card-front" aria-label="Business card front">
    <div class="front-brand">
      <span class="brand-dot"></span>
      <span class="brand-name">Clearwave Solutions</span>
    </div>
    <div class="rule" style="top:170px"></div>
    <div class="front-band">
      <div class="contact-col">
        <div class="person">DANIEL REYES<span class="role">Manager</span></div>
        <div class="line">
          <svg viewBox="0 0 18 16"><rect x="1" y="1" width="16" height="14" rx="2" fill="#fff"/><path d="M5 4c0 5 3 8 8 8l1-2-2-1-1 1c-2-1-3-2-4-4l1-1-1-2z" fill="#6fa9d3"/></svg>
          123 456 7890</div>
        <div class="line">
          <svg viewBox="0 0 18 16"><rect x="1" y="1" width="16" height="14" rx="2" fill="#fff"/><rect x="4" y="5" width="10" height="7" fill="#6fa9d3"/><rect x="6" y="3" width="6" height="3" fill="#6fa9d3"/></svg>
          123 456 7890</div>
      </div>
      <div class="divider"></div>
      <div class="contact-col right">
        <div class="line">
          <svg viewBox="0 0 18 16"><rect x="1" y="1" width="16" height="14" rx="2" fill="#fff"/><path d="M5 4c0 5 3 8 8 8l1-2-2-1-1 1c-2-1-3-2-4-4l1-1-1-2z" fill="#6fa9d3"/></svg>
          123 456 7890</div>
        <div class="line">
          <svg viewBox="0 0 18 16"><rect x="1" y="1" width="16" height="14" rx="2" fill="#fff"/><rect x="4" y="5" width="10" height="7" fill="#6fa9d3"/><rect x="6" y="3" width="6" height="3" fill="#6fa9d3"/></svg>
          123 456 7890</div>
        <div class="line">
          <svg viewBox="0 0 18 16"><rect x="1" y="1" width="16" height="14" rx="2" fill="#fff"/><path d="M4 5h10v7H4z" fill="#6fa9d3"/><path d="M4 5l5 4 5-4" stroke="#fff" fill="none"/></svg>
          hello@clearwavemedia.com</div>
      </div>
    </div>
    <div class="rule" style="top:292px"></div>
    <div class="front-address">Your Address, 2nd Ste, Elm Ridge, Oregon 4821</div>
  </section>

  <section class="card card-back" aria-label="Business card back">
    <div class="back-band top"></div>
    <div class="back-rule" style="top:114px"></div>
    <div class="back-center">www.clearwavemedia.com</div>
    <div class="back-rule" style="top:238px"></div>
    <div class="back-band bottom"></div>
  </section>

</main>
</body>
</html>
```